Business card design for my company.
I would like the card's background colour to be black. You can also see our web site to get an idea of our brand. https://www.tmwhomecrafting.com.au/
- Name
- Email

```html
<!DOCTYPE html>
<html lang="en">
<head>
<meta charset="utf-8">
<title>TMW Home Crafting – Business Card</title>
<link rel="stylesheet" href="https://fonts.googleapis.com/css2?family=Roboto:wght@400;500;700&family=Ubuntu:wght@500&display=swap">
<style>
  :root {
    --stage: #2a2a2a;
    --card: #262626;
    --card-edge: #1d1d1d;
    --green: #0f9a43;
    --white: #f4f4f4;
    --muted: #d8d8d8;
    --emboss: #4a4a4a;
  }
  * { box-sizing: border-box; margin: 0; padding: 0; }
  html, body { width: 1200px; height: 852px; overflow: hidden; }
  body {
    background: var(--stage);
    font-family: "Roboto", Arial, sans-serif;
    position: relative;
  }
  .card {
    position: absolute;
    top: 276px;
    width: 520px;
    height: 300px;
    border-radius: 18px;
    background: var(--card);
    overflow: hidden;
    border-bottom: 7px solid var(--green);
    box-shadow: 0 10px 30px rgba(0,0,0,.45);
  }
  .card--back { left: 50px; }
  .card--front { left: 630px; }

  /* Back */
  .back-brand {
    position: absolute;
    left: 0; right: 0; top: 100px;
    text-align: center;
    color: var(--emboss);
    font-weight: 700;
    font-size: 34px;
    letter-spacing: 3px;
    text-transform: uppercase;
  }
  .back-brand .mark {
    display: inline-block;
    width: 22px; height: 22px;
    background: var(--emboss);
    margin-right: 12px;
    vertical-align: -2px;
  }
  .back-web {
    position: absolute;
    left: 0; right: 0; bottom: 22px;
    text-align: center;
    color: var(--white);
    font-size: 14px;
  }

  /* Front */
  .front-brand {
    position: absolute;
    left: 38px; top: 58px;
    color: var(--white);
    font-weight: 700;
    font-size: 30px;
    line-height: 1.05;
    letter-spacing: 2px;
    text-transform: uppercase;
  }
  .front-brand .mark {
    display: inline-block;
    width: 18px; height: 18px;
    background: var(--green);
    margin-right: 10px;
  }
  .person {
    position: absolute;
    left: 38px; top: 196px;
  }
  .person__name {
    font-family: "Ubuntu", "Roboto", sans-serif;
    font-weight: 500;
    font-size: 21px;
    color: var(--green);
  }
  .person__role {
    font-size: 14px;
    color: var(--white);
    margin-top: 2px;
  }
  .contact {
    position: absolute;
    left: 318px; top: 86px;
    list-style: none;
    font-size: 12.5px;
    color: var(--muted);
  }
  .contact li {
    display: flex;
    align-items: center;
    height: 20px;
  }
  .contact svg { width: 12px; height: 12px; margin-right: 9px; flex: none; }
  .footer-strip {
    position: absolute;
    left: 0; bottom: 0;
    width: 300px; height: 14px;
    background: var(--white);
  }
  .footer-tab {
    position: absolute;
    right: 0; bottom: 0;
    width: 232px; height: 44px;
    background: var(--green);
    border-top-left-radius: 14px;
    color: var(--white);
    font-size: 13px;
    padding: 8px 0 0 24px;
  }
</style>
</head>
<body>

  <section class="card card--back" aria-label="Card back">
    <div class="back-brand"><span class="mark"></span>TMW Home Crafting</div>
    <div class="back-web">www.tmwhomecrafting.com.au</div>
  </section>

  <section class="card card--front" aria-label="Card front">
    <div class="front-brand"><span class="mark"></span>TMW<br>Home Crafting</div>

    <ul class="contact">
      <li>
        <svg viewBox="0 0 12 12"><path fill="#0f9a43" d="M2.5 1h2l1 3-1.3 1a6.5 6.5 0 0 0 2.8 2.8L8 6.5l3 1v2A1.5 1.5 0 0 1 9.5 11 8.5 8.5 0 0 1 1 2.5 1.5 1.5 0 0 1 2.5 1z"/></svg>
        0400 555 182
      </li>
      <li>
        <svg viewBox="0 0 12 12"><rect x="0.5" y="2.5" width="11" height="7" fill="#0f9a43"/><path d="M1 3l5 3.5L11 3" stroke="#262626" fill="none"/></svg>
        info@tmwhomecrafting.com.au
      </li>
      <li>
        <svg viewBox="0 0 12 12"><circle cx="6" cy="6" r="5" fill="#0f9a43"/><path d="M1 6h10M6 1c-2.5 3-2.5 7 0 10M6 1c2.5 3 2.5 7 0 10" stroke="#262626" stroke-width=".8" fill="none"/></svg>
        www.tmwhomecrafting.com.au
      </li>
      <li>
        <svg viewBox="0 0 12 12"><path fill="#0f9a43" d="M6 0.5a4 4 0 0 1 4 4c0 3-4 7-4 7s-4-4-4-7a4 4 0 0 1 4-4z"/><circle cx="6" cy="4.5" r="1.5" fill="#262626"/></svg>
        Riverton, Tasmania, Australia
      </li>
    </ul>

    <div class="person">
      <div class="person__name">Liam Carver</div>
      <div class="person__role">General Manager</div>
    </div>

    <div class="footer-strip"></div>
    <div class="footer-tab">TMW Home Crafting</div>
  </section>

</body>
</html>
```